LM-Steuerberatung WordPress Site fully implemented (tax advisor)

Hello!
I need a little Wordpress Site for my newly founded Tax-Advisor Company.
I am a one-man Office advising in the area of Crypto-Currency.
PLEASE only provide a Design, if you can also Implement a WP-Site afterwards on an existing Webspace.

Please find the Content and Website-Description in the attached Document

Language for the Website is German (for now)

Target Market(s)

Tax-Advisory (specialized in Crypto Currency)

Coding

Coded - Design and coding required

Number of Pages Required

5+ page

Font styles to use
Sans Serif

Requirements
Must have
• Wordpress Implementation afterwards - Details according to attached Project Information Document

```html
<!DOCTYPE html>
<html lang="de">
<head>
<meta charset="utf-8">
<title>LM-Steuerberatung</title>
<link rel="stylesheet" href="https://fonts.googleapis.com/css2?family=Montserrat:wght@600;700&family=Roboto:wght@500;700&display=swap">
<style>
  :root {
    --navy: #1a2a44;
    --navy-dark: #15233b;
    --gray: #a9a9a9;
    --gray-light: #eeeff0;
    --text-muted: #9a9a9a;
    --white: #ffffff;
  }
  * { box-sizing: border-box; margin: 0; padding: 0; }
  html, body { width: 1200px; height: 801px; overflow: hidden; background: var(--white); }
  body { position: relative; font-family: "Roboto", Arial, sans-serif; color: var(--navy); }

  .site-header {
    position: absolute; left: 0; top: 0; width: 1200px; height: 74px;
    background: var(--white); box-shadow: 0 4px 14px rgba(0,0,0,0.09); z-index: 5;
  }
  .brand {
    position: absolute; left: 110px; top: 25px; display: flex; align-items: center; gap: 8px;
    font-family: "Montserrat", Arial, sans-serif; font-weight: 700; font-size: 16px;
    letter-spacing: 0.2px; color: var(--navy);
  }
  .brand-mark { width: 22px; height: 22px; background: var(--navy); }
  .main-nav {
    position: absolute; top: 28px; left: 422px; display: flex; gap: 17px;
    font-size: 15px; font-weight: 500; color: var(--navy); align-items: center;
  }
  .caret { display: inline-block; width: 0; height: 0; margin-left: 10px; vertical-align: middle;
    border-left: 4.5px solid transparent; border-right: 4.5px solid transparent; border-top: 5px solid var(--navy); }
  .lang { display: flex; align-items: center; gap: 8px; margin-left: 6px; }
  .flag { width: 16px; height: 16px; border-radius: 50%; overflow: hidden;
    background: linear-gradient(#111 0 33%, #d00 33% 66%, #fc0 66%); }
  .btn {
    display: flex; align-items: center; justify-content: center; gap: 10px;
    background: var(--navy); color: var(--white); border-radius: 3px;
    font-weight: 700; text-transform: uppercase; letter-spacing: -0.2px;
  }
  .btn-icon { width: 13px; height: 13px; }
  .btn-header { position: absolute; left: 928px; top: 15px; width: 161px; height: 45px; font-size: 14px; }

  .hex-deco-left { position: absolute; left: 0; top: 124px; }
  .wave-band {
    position: absolute; left: 0; top: 610px; width: 1200px; height: 191px;
    background:
      radial-gradient(ellipse 420px 90px at 200px 95px, rgba(190,190,190,0.55), transparent 70%),
      radial-gradient(ellipse 380px 70px at 820px 60px, rgba(200,200,200,0.5), transparent 70%),
      radial-gradient(ellipse 260px 80px at 1150px 90px, rgba(185,185,185,0.5), transparent 70%);
  }

  .hero-eyebrow {
    position: absolute; left: 110px; top: 211px; font-family: "Montserrat", Arial, sans-serif;
    font-weight: 700; font-size: 17px; color: var(--text-muted); text-transform: uppercase;
  }
  .hero-title {
    position: absolute; left: 108px; top: 250px; width: 460px; font-family: "Montserrat", Arial, sans-serif;
    font-weight: 700; font-size: 30.5px; line-height: 43px; color: var(--navy); text-transform: uppercase;
  }
  .hero-lead {
    position: absolute; left: 111px; top: 401px; width: 420px; font-size: 16.3px; line-height: 24px;
    font-weight: 500; color: var(--navy);
  }
  .btn-hero { position: absolute; left: 111px; top: 478px; width: 283px; height: 56px; font-size: 14px; }

  .slider-arrow {
    position: absolute; top: 369px; width: 38px; height: 38px; border-radius: 50%;
    border: 1px solid #999; background: var(--white); display: flex; align-items: center; justify-content: center;
  }
  .slider-arrow.prev { left: 33px; }
  .slider-arrow.next { left: 1129px; }

  .hero-graphic { position: absolute; left: 600px; top: 170px; }
  .dot-field {
    position: absolute; left: 650px; top: 525px; width: 100px; height: 52px;
    background: linear-gradient(90deg, rgba(26,42,68,0.18), rgba(26,42,68,0.1));
    border-radius: 2px;
  }
</style>
</head>
<body>
  <header class="site-header">
    <div class="brand"><span class="brand-mark"></span>LM STEUERBERATUNG</div>
    <nav class="main-nav">
      <span>Heim</span>
      <span>Leistungen<span class="caret"></span></span>
      <span>Über mich</span>
      <span>Kontakt</span>
      <span>Impressum</span>
      <span class="lang"><span class="flag"></span>Ger<span class="caret"></span></span>
    </nav>
    <a class="btn btn-header">Jetzt loslegen
      <svg class="btn-icon" viewBox="0 0 14 14"><circle cx="7" cy="7" r="7" fill="#fff"/><path d="M5.5 4 L8.5 7 L5.5 10" stroke="#1a2a44" stroke-width="2" fill="none"/></svg>
    </a>
  </header>

  <svg class="hex-deco-left" width="170" height="470" viewBox="0 0 170 470">
    <path d="M0 42 L70 0 L160 52 L160 62 L45 130 L45 340 L160 405 L70 467 L0 428 Z" fill="var(--gray-light)"/>
  </svg>

  <div class="wave-band" role="img" aria-label="Geschwungenes Feinlinienband als Hintergrunddekoration"></div>

  <p class="hero-eyebrow">Willkommen bei LM-Steuerberatung!</p>
  <h1 class="hero-title">Dann melde ich einfach meinen Hauptwohnsitz in Österreich ab</h1>
  <p class="hero-lead">Ihrem Spezialisten bei allen steuerlichen Themen rund um Einkünfte &amp; Vermögen aus Krypto-Assets.</p>
  <a class="btn btn-hero">Weiter zu unseren Leistungen
    <svg class="btn-icon" viewBox="0 0 14 14"><circle cx="7" cy="7" r="7" fill="#fff"/><path d="M5.5 4 L8.5 7 L5.5 10" stroke="#1a2a44" stroke-width="2" fill="none"/></svg>
  </a>

  <div class="slider-arrow prev"><svg width="12" height="18" viewBox="0 0 12 18"><path d="M9 2 L3 9 L9 16" stroke="#111" stroke-width="2" fill="none"/></svg></div>
  <div class="slider-arrow next"><svg width="12" height="18" viewBox="0 0 12 18"><path d="M3 2 L9 9 L3 16" stroke="#111" stroke-width="2" fill="none"/></svg></div>

  <svg class="hero-graphic" width="530" height="440" viewBox="0 0 530 440">
    <defs>
      <linearGradient id="photoTone" x1="0" y1="0" x2="1" y2="1">
        <stop offset="0" stop-color="#d9dcd8"/>
        <stop offset="0.5" stop-color="#6e7560"/>
        <stop offset="1" stop-color="#2f3330"/>
      </linearGradient>
    </defs>
    <path d="M8 48 L78 8 L130 38 L100 78 L77 90 L77 260 L100 300 L78 293 L8 253 Z" fill="var(--navy)"/>
    <path d="M397 62 L460 30 L521 66 L521 200 L440 246 L433 230 L433 120 L397 95 Z" fill="var(--gray)"/>
    <path d="M261 10 Q268 7 276 11 L436 103 Q446 109 446 120 L446 300 Q446 311 436 317 L276 409 Q268 413 261 409 L101 317 Q91 311 91 300 L91 120 Q91 109 101 103 Z"
          fill="url(#photoTone)" stroke="var(--navy)" stroke-width="4" role="img" aria-label="Foto: Steuerberater am Schreibtisch mit Laptop und Kursdiagramm"/>
  </svg>
  <div class="dot-field" role="img" aria-label="Punktraster als Dekoration"></div>
</body>
</html>
```